Business Card Design

New business card design

Target Market(s)

Residential & Commercial Property Managers

Industry/Entity Type

Plumbing Services

Contact Information for Business Card

Name - Rowan Keddle, title - Director, Phone Number - 0431 286 517, email - rowan@tbk-plumbing.com.au, Company ABN - 73 215 904 386,

Font styles to use
Sans Serif

Colors
0054AA
0677BA
7BADD7
CADEEF
E8F1F8

```html
<!DOCTYPE html>
<html lang="en">
<head>
<meta charset="utf-8">
<title>TBK Plumbing Services – Business Card</title>
<link rel="stylesheet" href="https://fonts.googleapis.com/css2?family=Lexend+Exa:wght@300&family=Roboto:wght@300;400&display=swap">
<style>
  :root {
    --backdrop: #c4c4c4;
    --card-light: #ffffff;
    --card-dark: #1d222a;
    --ink: #1f242b;
    --ink-soft: #3a3f45;
    --accent: #1aaee9;
    --rule: #9a9a9a;
  }
  html, body {
    margin: 0;
    padding: 0;
    width: 1093px;
    height: 1200px;
    overflow: hidden;
    background: var(--backdrop);
  }
  .canvas {
    position: relative;
    width: 1093px;
    height: 1200px;
    font-family: "Roboto", Arial, sans-serif;
  }
  .card {
    position: absolute;
    left: 264px;
    width: 580px;
    height: 356px;
    border-radius: 28px;
    overflow: hidden;
  }
  .card--front { top: 226px; background: var(--card-light); }
  .card--back  { top: 621px; background: var(--card-dark); }

  .brand {
    position: absolute;
    display: flex;
    flex-direction: column;
    align-items: center;
    font-family: "Roboto", Arial, sans-serif;
    font-weight: 300;
  }
  .brand__name {
    display: flex;
    align-items: center;
    gap: 10px;
    line-height: 1;
    letter-spacing: 2px;
  }
  .brand__dot {
    border-radius: 50%;
    background: var(--accent);
  }
  .brand__tagline {
    letter-spacing: 0.62em;
    margin-right: -0.62em;
  }

  .card--front .brand { left: 40px; width: 250px; top: 132px; color: var(--ink); }
  .card--front .brand__name { font-size: 58px; }
  .card--front .brand__dot { width: 12px; height: 12px; }
  .card--front .brand__tagline { font-size: 9.5px; margin-top: 16px; color: var(--ink-soft); }

  .divider {
    position: absolute;
    left: 289px;
    top: 74px;
    width: 1px;
    height: 209px;
    background: linear-gradient(to bottom, transparent, var(--rule) 15%, var(--rule) 85%, transparent);
  }

  .contact {
    position: absolute;
    left: 312px;
    top: 100px;
    color: var(--ink);
  }
  .contact__name {
    font-family: "Lexend Exa", "Roboto", sans-serif;
    font-weight: 300;
    font-size: 22px;
    line-height: 1;
    margin: 0;
    letter-spacing: -0.5px;
  }
  .contact__title {
    font-weight: 300;
    font-size: 17px;
    color: var(--accent);
    margin: 2px 0 0;
  }
  .contact__list {
    list-style: none;
    margin: 22px 0 0;
    padding: 0;
    font-weight: 300;
    font-size: 17px;
    line-height: 21px;
  }
  .contact__list li {
    display: flex;
    align-items: center;
    gap: 6px;
  }
  .contact__icon { width: 16px; height: 16px; flex: none; }
  .contact__abn {
    margin: 19px 0 0 -1px;
    font-weight: 300;
    font-size: 17px;
  }
  .contact__abn-label { color: var(--accent); }

  .card--back .brand { left: 0; right: 0; top: 120px; color: #ffffff; }
  .card--back .brand__name { font-size: 84px; }
  .card--back .brand__dot { width: 16px; height: 16px; }
  .card--back .brand__tagline { font-size: 13px; margin-top: 24px; }
</style>
</head>
<body>
<main class="canvas">

  <section class="card card--front" aria-label="Business card front">
    <div class="brand">
      <div class="brand__name"><span>tbk</span><span class="brand__dot"></span></div>
      <div class="brand__tagline">plumbing services</div>
    </div>

    <div class="divider"></div>

    <div class="contact">
      <h1 class="contact__name">Rowan Keddle</h1>
      <p class="contact__title">Director</p>
      <ul class="contact__list">
        <li>
          <svg class="contact__icon" viewBox="0 0 24 24" aria-hidden="true">
            <path fill="var(--ink)" d="M6.6 10.8a15.2 15.2 0 0 0 6.6 6.6l2.2-2.2c.3-.3.7-.4 1-.2 1.1.4 2.3.6 3.6.6.6 0 1 .4 1 1V20c0 .6-.4 1-1 1C10.6 21 3 13.4 3 4c0-.6.4-1 1-1h3.5c.6 0 1 .4 1 1 0 1.3.2 2.5.6 3.6.1.3 0 .7-.2 1z"/>
            <path fill="none" stroke="var(--ink)" stroke-width="1.6" d="M14 3.5a7 7 0 0 1 6.5 6.5M14 7a3.5 3.5 0 0 1 3 3"/>
          </svg>
          <span>0431 286 517</span>
        </li>
        <li>
          <svg class="contact__icon" viewBox="0 0 24 24" aria-hidden="true">
            <rect x="1" y="5" width="22" height="14" fill="var(--ink)"/>
            <path fill="none" stroke="#fff" stroke-width="1.4" d="M1.5 5.5 12 13l10.5-7.5M1.5 18.5 9 11.5M22.5 18.5 15 11.5"/>
          </svg>
          <span>rowan@tbk-plumbing.com.au</span>
        </li>
      </ul>
      <p class="contact__abn"><span class="contact__abn-label">Company ABN</span> - 73 215 904 386</p>
    </div>
  </section>

  <section class="card card--back" aria-label="Business card back">
    <div class="brand">
      <div class="brand__name"><span>tbk</span><span class="brand__dot"></span></div>
      <div class="brand__tagline">plumbing services</div>
    </div>
  </section>

</main>
</body>
</html>
```